TK Homes - Stone Dorf Design

Looking for a double sides design, 1 side for my realestate and the other for home building. ( TK Homes on 1 side, Stone Dorf card on the other Side
Side 1 - Marek Tove ~ Vox Realty logo and Company ( the Property quarter )
Marek Tove
Marek@Marektove.example
IG - Marek_Bzq_Realtor
FB - marekt
Cell - 5558130467
3847 61 St Nw

Side 2
Marek Tove
5558130467
IG - Stonedorf_Bzq
Stonedorfdev@mailbox.example

Target Market(s)

Home buyers/ sellers

Industry/Entity Type

Home builders - Realestate

Contact Information for Business Card

Above

Requirements
Must have
• Black OR White background - my information -

```html
<!DOCTYPE html>
<html lang="en">
<head>
<meta charset="utf-8">
<title>Marek Tove – Business Cards</title>
<link href="https://fonts.googleapis.com/css2?family=Tinos:wght@400;700&display=swap" rel="stylesheet">
<style>
  :root{
    --page:#1f1f21;
    --card:#222226;
    --blue:#0a74c2;
    --red:#e04b3f;
    --white:#ffffff;
  }
  *{box-sizing:border-box;margin:0;padding:0}
  html,body{width:1200px;height:780px;overflow:hidden;background:var(--page)}
  body{font-family:"Tinos","Times New Roman",serif;display:flex;align-items:center;justify-content:center;gap:40px}
  .card{position:relative;width:560px;height:320px;background:var(--card);overflow:hidden;box-shadow:0 10px 30px rgba(0,0,0,.55)}
  .swoosh{position:absolute;inset:0;width:100%;height:100%}
  .brand{position:absolute;top:30px;left:0;width:100%;text-align:center;color:var(--blue);font-size:40px;font-weight:400;letter-spacing:3px}
  .person{position:absolute;left:56px;top:156px}
  .person-name{font-size:34px;font-weight:700;white-space:nowrap}
  .first{color:var(--blue)}
  .last{color:var(--red)}
  .person-role{color:var(--white);font-weight:700;font-size:15px;text-align:right;margin-top:-4px}
  .divider{position:absolute;left:300px;width:2px;background:var(--white)}
  .contacts{position:absolute;left:322px;list-style:none;color:var(--white);font-size:14px;line-height:19px}
  .contacts li{display:flex;align-items:center;gap:8px;white-space:nowrap}
  .icon{width:13px;height:13px;flex:none;fill:var(--blue)}
  .dot{width:11px;height:11px;border-radius:50%;background:var(--blue);flex:none;margin:0 1px}
  .address{position:absolute;left:322px;top:190px;color:var(--white);font-size:15px}
  .card--builder .contacts{top:112px}
  .card--builder .divider{top:110px;height:100px}
  .card--realty .contacts{top:86px}
  .card--realty .divider{top:92px;height:118px}
</style>
</head>
<body>

<section class="card card--builder">
  <svg class="swoosh" viewBox="0 0 560 320" aria-hidden="true">
    <path d="M0,300 C230,285 420,255 560,215 L560,320 L0,320 Z" fill="var(--blue)"/>
    <path d="M40,290 C250,270 430,235 535,195" fill="none" stroke="var(--red)" stroke-width="3"/>
  </svg>
  <div class="brand">STONE DORF</div>
  <div class="person">
    <div class="person-name"><span class="first">Marek</span> <span class="last">Tove</span></div>
    <div class="person-role">Director</div>
  </div>
  <div class="divider"></div>
  <ul class="contacts">
    <li><svg class="icon" viewBox="0 0 24 24"><path d="M6.6 10.8a15 15 0 0 0 6.6 6.6l2.2-2.2a1 1 0 0 1 1-.25 11.4 11.4 0 0 0 3.6.57 1 1 0 0 1 1 1V20a1 1 0 0 1-1 1A17 17 0 0 1 3 4a1 1 0 0 1 1-1h3.5a1 1 0 0 1 1 1c0 1.25.2 2.450.57 3.6a1 1 0 0 1-.25 1z"/></svg>5558130467</li>
    <li><span class="dot"></span>Stonedorf_Bzq</li>
    <li><svg class="icon" viewBox="0 0 24 24"><path d="M2 5h20v14H2z M2 5l10 8 10-8"/></svg>Stonedorfdev@mailbox.example</li>
  </ul>
</section>

<section class="card card--realty">
  <svg class="swoosh" viewBox="0 0 560 320" aria-hidden="true">
    <path d="M0,300 C230,285 420,255 560,215 L560,320 L0,320 Z" fill="var(--blue)"/>
    <path d="M40,290 C250,270 430,235 535,195" fill="none" stroke="var(--red)" stroke-width="3"/>
  </svg>
  <div class="brand">MAREK TOVE</div>
  <div class="person">
    <div class="person-name"><span class="first">Marek</span> <span class="last">Tove</span></div>
    <div class="person-role">Director</div>
  </div>
  <div class="divider"></div>
  <ul class="contacts">
    <li><svg class="icon" viewBox="0 0 24 24"><path d="M6.6 10.8a15 15 0 0 0 6.6 6.6l2.2-2.2a1 1 0 0 1 1-.25 11.4 11.4 0 0 0 3.6.57 1 1 0 0 1 1 1V20a1 1 0 0 1-1 1A17 17 0 0 1 3 4a1 1 0 0 1 1-1h3.5a1 1 0 0 1 1 1c0 1.25.2 2.45.57 3.6a1 1 0 0 1-.25 1z"/></svg>5558130467</li>
    <li><span class="dot"></span>marekt</li>
    <li><span class="dot"></span>Marek_Bzq_Realtor</li>
    <li><svg class="icon" viewBox="0 0 24 24"><path d="M2 5h20v14H2z M2 5l10 8 10-8"/></svg>Marek@Marektove.example</li>
    <li><svg class="icon" viewBox="0 0 24 24" fill="none" stroke="var(--blue)" stroke-width="2"><circle cx="12" cy="12" r="10"/><path d="M2 12h20M12 2c3 3 3 17 0 20M12 2c-3 3-3 17 0 20"/></svg>www.marektove.example</li>
  </ul>
  <div class="address">3847 61 St Nw</div>
</section>

</body>
</html>
```